Media Services Start-up -- Corporate Website and Logo Design. Inspiration required!

We need a logo design and corporate website design, including coding, for our start-up business.
Vennatra’s value proposition is based on bringing together media content from a vast number of geographies globally, adding human and AI curation, translation and editing, and delivering the content using tailored customer interfaces. On the one hand, the business brings together media coverage from all over the world, and on the other it brings together content, human skills and technology to deliver a supreme customer experience.
Vennatra is a B2B media monitoring and analytics business with emphasis on global customers. Vennatra's service offering is centred around sourcing media content from different markets, processing, storing and delivering the content and insights derived from it using an online platform / mobile app.
The messaging we want to create through the logo is:
- Global scope
- Speed of delivery
- Cost-efficiency
- Multi-lingual
- Tailor-made
- Trustworthy
Target Market(s)
Business to business, PR / Communications, Media, Marketing
Logo Text
Vennatra
Coding
Coded - Design and coding required
Number of Pages Required
5+ page
Font styles to use
Other font styles liked:
- See Design Brief for details
Colors
Designer to choose colors to be used in the design.

```html
<!DOCTYPE html>
<html lang="en">
<head>
<meta charset="utf-8">
<title>Vennatra — Delivering Global Media Intelligence</title>
<link rel="stylesheet" href="https://fonts.googleapis.com/css2?family=Roboto:wght@400;500;700&display=swap">
<style>
  :root {
    --ink: #111111;
    --white: #ffffff;
    --teal: #3aaf9f;
    --hero-dark: #1f2630;
    --hero-mid: #3a4654;
    --hero-warm: #5a4a44;
    --field-border: #333333;
    --placeholder: #555555;
  }
  * { box-sizing: border-box; margin: 0; padding: 0; }
  html, body { width: 1200px; height: 747px; overflow: hidden; background: var(--white); }
  body { font-family: "Roboto", Arial, sans-serif; color: var(--ink); position: relative; }

  .site-header { position: absolute; left: 0; top: 0; width: 1200px; height: 71px; background: var(--white); }
  .brand { position: absolute; left: 143px; top: 16px; font-size: 29px; font-weight: 700; letter-spacing: -0.3px; }
  .main-nav a { position: absolute; top: 26px; font-size: 14px; color: var(--ink); text-decoration: none; }
  .btn-signin { position: absolute; left: 967px; top: 18px; width: 92px; height: 35px; background: var(--teal);
    color: var(--white); font-size: 15px; display: flex; align-items: center; justify-content: center;
    border-radius: 2px; box-shadow: 0 2px 5px rgba(0,0,0,.2); }

  .hero { position: absolute; left: 0; top: 71px; width: 1200px; height: 640px; }
  .hero svg { position: absolute; inset: 0; }
  .hero-title { position: absolute; left: 140px; top: 198px; color: var(--white); font-size: 40px; font-weight: 700;
    line-height: 58px; letter-spacing: 0.2px; text-shadow: 0 2px 4px rgba(0,0,0,.5); }
  .hero-copy { position: absolute; left: 142px; top: 327px; width: 460px; color: var(--white); font-family: Arial, "Roboto", sans-serif;
    font-size: 16px; line-height: 25.5px; }

  .lead-card { position: absolute; left: 766px; top: 214px; width: 293px; height: 336px; background: var(--white); border-radius: 6px; }
  .lead-card svg { position: absolute; left: 3px; top: 3px; }
  .lead-card h2 { position: absolute; left: 0; top: 19px; width: 100%; text-align: center; color: var(--white); font-size: 17px; font-weight: 500; }
  .field { position: absolute; left: 32px; width: 228px; height: 37px; border: 1px solid var(--field-border); border-radius: 3px;
    padding-left: 13px; display: flex; align-items: center; font-size: 12.5px; color: var(--placeholder); }
  .btn-start { position: absolute; left: 57px; top: 268px; width: 178px; height: 35px; background: var(--teal); color: var(--white);
    font-size: 15px; display: flex; align-items: center; justify-content: center; border-radius: 2px; }

  .site-footer .legal { position: absolute; left: 142px; top: 717px; font-size: 12.5px; }
  .social { position: absolute; top: 715px; width: 22px; height: 22px; border-radius: 50%; background: var(--ink); }
</style>
</head>
<body>
  <header class="site-header">
    <div class="brand">Vennatra</div>
    <nav class="main-nav">
      <a href="#" style="left:363px">Home</a>
      <a href="#" style="left:455px">Solutions</a>
      <a href="#" style="left:568px">How We Do It</a>
      <a href="#" style="left:707px">Our People</a>
      <a href="#" style="left:829px">Our Technology</a>
    </nav>
    <a class="btn-signin">SIGN IN</a>
  </header>

  <section class="hero">
    <svg width="1200" height="640" viewBox="0 0 1200 640" role="img" aria-label="Dimmed photo of a hand with a fountain pen reviewing printed charts and reports">
      <defs>
        <linearGradient id="heroTone" x1="0" y1="0" x2="1" y2="1">
          <stop offset="0" stop-color="#4a4340"/>
          <stop offset="0.35" stop-color="#2c333d"/>
          <stop offset="0.7" stop-color="#262d37"/>
          <stop offset="1" stop-color="#3a4450"/>
        </linearGradient>
      </defs>
      <path d="M0 0 H1200 V558 Q600 780 0 558 Z" fill="url(#heroTone)"/>
    </svg>
    <h1 class="hero-title">DELIVERING GLOBAL MEDIA<br>INTELLIGENCE</h1>
    <p class="hero-copy">Vennatra is an international media intelligence service provider. We help communications teams builds and operate truly global media monitoring and measurement programmes.</p>
  </section>

  <aside class="lead-card">
    <svg width="287" height="58" viewBox="0 0 287 58"><path d="M0 6 Q0 0 6 0 H281 Q287 0 287 6 V39 Q143 80 0 39 Z" fill="var(--ink)"/></svg>
    <h2>Learn More About Vennatra</h2>
    <div class="field" style="top:88px">Name</div>
    <div class="field" style="top:145px">Email Address</div>
    <div class="field" style="top:201px">Phone</div>
    <a class="btn-start">GET STARTED</a>
  </aside>

  <footer class="site-footer">
    <p class="legal">© 2019 Vennatra Analytics Media. All rights reserved.</p>
    <span class="social" style="left:951px"></span>
    <span class="social" style="left:979px"></span>
    <span class="social" style="left:1008px"></span>
    <span class="social" style="left:1036px"></span>
  </footer>
</body>
</html>
```